Luxury Tours Design

We are “Amber Coachline” a Chauffeur Company based in Maidenhead, Berkshire. Our website is - ambercoachline.co.uk which will give you an insite into the Company.
Our clients consist of luxurious Hotels, large Corporate Companies along with private UHNW clients.
We have a fleet of Valtrane E, S and V Class vehicles along with 16 Seater Executive Coaches so we can accommodate single travellers, couples, friends, families and groups.
We would like an A5 (or slightly larger) double sided colour leaflet designed to promote our Tours in our local and surrounding areas.
The information below is some indication as to what we would like.
On the front we would like:-
Amber Coachline “Signature Tour” This will be our main promoting Tour
Slogan “Amber Coachline….ever at your service”
Tour will include:-
Visiting the historic town of Windsor, Hollenby Castle, St Aldric’s Chapel and Regal Pemberly Shopping Arcade.
Then onto Eton (Dunmere College) and a lovely view of the River Thames along with an array of Antique Shops in the quaint streets.
Bray Village (Heron Isle), renowed for it’s Brevard Star Restaurants and pubs.
Through picturesque Cookham along to Marlow for some shopping in the boutique shops, small listed buildings and beautiful places for refreshments, along with stunning views of the River Thames form Ashcombe Bridge.
This will be our main tour we offer but again this is flexible. This aims to be around 4-5 hours.
On the front, a picture of Hollenby castle maybe a large picture with writing over the top, or a separate photo….. a couple of photos attached or something similar.
On the back of the leaflet:-
We offer London based tours including:-
Belvards, Larkmoor Park, Ravensholt Palace, Corringdale Palace, Pellington Square, Turning of the Sentries, Keep of Ardmoor, Tall Tom, Glenmoreton Abbey to name a few! Or maybe London by night with a show or restaurant.
On the back a picture of Corringdale Palace…a couple of picture are also attached or again something similar.
Other Tours provided:-
Ridgewell Court Palace, Oxford and Corvane Palace, Ashmarrow Ring and Bath, The Cotswolds, Stratford and Penlow Castle, Quillford Shopping Village.
Also bespoke Tours can be arranged. We can personalise any tour to your requirements.
Experienced friendly Chauffeur’s, no request too big or small.
Please call us on 01632 960417 or email us sales@ambercoachline.co.uk
Please can you do an initial design including the above information.
Look forward to hearing from you.
Kind regards
Please visit https://www.hartleyprivatedrives.co.uk/ to get an idea of the tours of London to go on the back.
Prices will follow to be added after design and layout has been done.
Our AC logo is available on www.ambercoachline.co.uk
We want text to be editable and also for the design to have a luxury feel.
Chauffeur

```html
<!DOCTYPE html>
<html lang="en">
<head>
<meta charset="utf-8">
<title>Amber Coachline – Tours Leaflet</title>
<link rel="stylesheet" href="https://fonts.googleapis.com/css2?family=Great+Vibes&family=Poppins:ital,wght@0,400;0,500;0,600;1,400;1,600&display=swap">
<style>
  :root{
    --canvas:#ffffff;
    --ink-dark:#2a2822;
    --script:#4a4530;
    --panel:rgba(120,108,70,0.82);
    --gold:#e2cc6a;
    --gold-deep:#a08c3e;
    --white:#ffffff;
    --text-dark:#26241f;
  }
  *{margin:0;padding:0;box-sizing:border-box}
  html,body{width:800px;height:1200px;overflow:hidden;background:var(--canvas)}
  body{position:relative;font-family:"Poppins",sans-serif}
  .leaflet{position:absolute;left:214px;width:372px;height:527px;overflow:hidden;background:var(--ink-dark);box-shadow:0 2px 8px rgba(0,0,0,.35)}
  .leaflet--front{top:53px}
  .leaflet--back{top:629px}
  .abs{position:absolute}
  .script{font-family:"Great Vibes",cursive;font-weight:400;white-space:nowrap}

  /* front */
  .hero-castle{position:absolute;left:0;top:0;width:372px;height:315px;
    background:linear-gradient(180deg,#c9d6de 0%,#e6cfc6 22%,#ee9f8e 36%,#8f8a78 46%,#4f7a2e 58%,#3d6a24 78%,#2a2822 100%)}
  .title{left:0;width:100%;text-align:center;color:var(--script)}
  .front-title{top:10px;font-size:46px}
  .front-slogan{top:64px;font-size:21px;color:#3d3a2c}
  .fleet{left:30px;width:312px;top:237px;text-align:center;color:var(--white);font-size:9px;line-height:10.8px}
  .tour-panel{left:44px;top:290px;width:284px;height:160px;background:var(--panel)}
  .tour-heading{left:11px;top:5px;color:var(--gold);font-size:12.2px;line-height:12.4px;font-weight:400}
  .price{left:230px;top:8px;width:45px;height:15px;background:var(--gold-deep);color:var(--white)}
  .price small{position:absolute;left:6px;top:1px;font-size:2.4px}
  .price b{position:absolute;left:6px;top:3.5px;font-size:8.5px;font-weight:600;line-height:10px}
  .tour-text{left:11px;top:40px;width:262px;color:var(--white);font-size:6.2px;line-height:7.4px}
  .tour-text p{margin-bottom:7.2px}
  .quote{color:var(--gold);font-style:italic;text-align:center;left:0;width:100%}
  .quote .mark{font-weight:600;font-style:normal;font-size:11px;vertical-align:-2px}
  .front-quote{top:135px;font-size:8.4px}

  /* contact block */
  .contact-label{left:0;width:100%;text-align:center;color:var(--gold);font-size:5.8px;letter-spacing:1.3px;font-weight:500}
  .contact-row{left:42px;width:290px;display:flex;align-items:center;justify-content:space-between;color:var(--white);font-size:6px;font-weight:500}
  .contact-row .item{display:flex;align-items:center;gap:3px}
  .contact-row .phone{font-size:7.4px}
  .contact-row .sep{width:1px;height:8px;background:rgba(255,255,255,.5)}
  .contact-row svg{width:8px;height:8px}
  .brand{left:0;width:100%;display:flex;justify-content:center;align-items:center;gap:4px;color:var(--white);font-size:11px;font-weight:400}
  .brand .dot{width:15px;height:15px;border-radius:50%;background:#c8c4b8}

  /* back */
  .hero-palace{position:absolute;left:0;top:0;width:372px;height:325px;
    background:linear-gradient(180deg,#c2d3df 0%,#e3dad6 28%,#f0b9a4 42%,#d9d3cc 52%,#b5b1a8 60%,#d7c040 66%,#c8322a 78%,#8a8a2a 88%,#2a2822 100%)}
  .back-title{top:8px;font-size:38px}
  .place-list{list-style:none;color:var(--text-dark);font-size:8.4px;line-height:14.2px}
  .by-night{left:34px;top:110px;font-size:8.2px;font-weight:600;font-style:italic;color:var(--text-dark)}
  .others-panel{left:36px;top:312px;width:300px;height:137px;background:var(--panel)}
  .others-title{left:0;width:100%;text-align:center;top:2px;font-size:25px;color:var(--gold)}
  .others-list{list-style:none;color:var(--white);font-size:6.6px;line-height:14px;text-transform:uppercase}
  .back-quote{top:93px;font-size:7px;line-height:8.4px}
  .on-request{left:0;width:100%;text-align:center;top:118px;color:var(--gold);font-size:8px}
</style>
</head>
<body>

<section class="leaflet leaflet--front">
  <div class="hero-castle" role="img" aria-label="Photograph of a historic castle at sunset above a long tree-lined avenue"></div>
  <h1 class="abs title script front-title">Signature Tour</h1>
  <p class="abs title script front-slogan">Amber Coachline..ever at your service..</p>
  <p class="abs fleet">We have a fleet of Valtrane E, S and V Class vehicles along with 16 Seater Executive Coaches so we can accommodate single travellers, couples, friends, families and groups.</p>

  <div class="abs tour-panel">
    <h2 class="abs tour-heading">VISIT TO THE HISTORIC<br>TOWN OF WINDSOR</h2>
    <div class="abs price"><small>FROM</small><b>£350.00</b></div>
    <div class="abs tour-text">
      <p>Visiting the historic town of Windsor, Hollenby Castle, St Aldric’s Chapel and Regal Pemberly Shopping Arcade.</p>
      <p>Eton and Dunmere College with lovely views of the River Thames along with an array of Antique Shops in the quaint streets.</p>
      <p>Bray Village renowned for it's Brevard Star restaurants and pubs, along with a visit to Heron Isle.</p>
      <p>Through picturesque Cookham along to Marlow for some shopping in the boutique shops, small listed buildings and beautiful places for refreshments, along with stunning views of the River Thames from Ashcombe Bridge.</p>
    </div>
    <p class="abs quote front-quote"><span class="mark">“</span>Our signature tour is approximately 4 hours<span class="mark">”</span></p>
  </div>

  <p class="abs contact-label" style="top:459px">CONTACT US</p>
  <div class="abs contact-row" style="top:471px">
    <span class="item"><svg viewBox="0 0 16 16"><circle cx="8" cy="8" r="7" fill="none" stroke="#e2cc6a" stroke-width="1.2"/><rect x="4" y="5.5" width="8" height="5.5" fill="none" stroke="#e2cc6a" stroke-width="1"/><path d="M4 5.5 8 8.6 12 5.5" fill="none" stroke="#e2cc6a" stroke-width="1"/></svg>sales@ambercoachline.co.uk</span>
    <span class="sep"></span>
    <span class="item phone"><svg viewBox="0 0 16 16"><circle cx="8" cy="8" r="7" fill="none" stroke="#e2cc6a" stroke-width="1.2"/><path d="M5.5 4.5c-.8.8-.6 2.6 1.3 4.6s3.7 2.2 4.6 1.3l-1.3-1.3-1 .6-2.3-2.3.6-1z" fill="none" stroke="#e2cc6a" stroke-width="1"/></svg>01632 960417</span>
    <span class="sep"></span>
    <span class="item"><svg viewBox="0 0 16 16"><circle cx="8" cy="8" r="7" fill="none" stroke="#e2cc6a" stroke-width="1.2"/><circle cx="8" cy="8" r="4" fill="none" stroke="#e2cc6a" stroke-width="1"/><path d="M4 8h8M8 4v8" stroke="#e2cc6a" stroke-width="1"/></svg>www.ambercoachline.co.uk</span>
  </div>
  <div class="abs brand" style="top:496px"><span class="dot"></span>Amber Coachline</div>
</section>

<section class="leaflet leaflet--back">
  <div class="hero-palace" role="img" aria-label="Photograph of a grand palace with a memorial statue behind beds of red and yellow tulips"></div>
  <h1 class="abs title script back-title">London Tours</h1>
  <ul class="abs place-list" style="left:34px;top:57px"><li>Belvards</li><li>Larkmoor Park</li><li>Ravensholt Palace</li></ul>
  <ul class="abs place-list" style="left:134px;top:57px"><li>Corringdale Palace</li><li>Pellington Square</li><li>Turning of the Sentries</li></ul>
  <ul class="abs place-list" style="left:259px;top:55px"><li>Keep of Ardmoor</li><li>Tall Tom</li><li>Glenmoreton Abbey</li></ul>
  <p class="abs by-night">Or maybe London by night with a show or restaurant.</p>

  <div class="abs others-panel">
    <h2 class="abs script others-title">Other Tours Available</h2>
    <ul class="abs others-list" style="left:23px;top:40px"><li>Ridgewell Court Palace</li><li>Oxford and Corvane Palace</li><li>Ashmarrow Ring and Bath</li></ul>
    <ul class="abs others-list" style="left:160px;top:40px"><li>The Cotswolds</li><li>Stratford and Penlow Castle</li><li>Quillford Shopping Village</li></ul>
    <p class="abs quote back-quote"><span class="mark">“</span>Also bespoke tours can be arranged. We can personalize any tour to <span class="mark">”</span><br>your requirements with our friendly, experienced chauffeurs</p>
    <p class="abs on-request">Prices On Request</p>
  </div>

  <p class="abs contact-label" style="top:459px">CONTACT US</p>
  <div class="abs contact-row" style="top:471px">
    <span class="item"><svg viewBox="0 0 16 16"><circle cx="8" cy="8" r="7" fill="none" stroke="#e2cc6a" stroke-width="1.2"/><rect x="4" y="5.5" width="8" height="5.5" fill="none" stroke="#e2cc6a" stroke-width="1"/><path d="M4 5.5 8 8.6 12 5.5" fill="none" stroke="#e2cc6a" stroke-width="1"/></svg>sales@ambercoachline.co.uk</span>
    <span class="sep"></span>
    <span class="item phone"><svg viewBox="0 0 16 16"><circle cx="8" cy="8" r="7" fill="none" stroke="#e2cc6a" stroke-width="1.2"/><path d="M5.5 4.5c-.8.8-.6 2.6 1.3 4.6s3.7 2.2 4.6 1.3l-1.3-1.3-1 .6-2.3-2.3.6-1z" fill="none" stroke="#e2cc6a" stroke-width="1"/></svg>01632 960417</span>
    <span class="sep"></span>
    <span class="item"><svg viewBox="0 0 16 16"><circle cx="8" cy="8" r="7" fill="none" stroke="#e2cc6a" stroke-width="1.2"/><circle cx="8" cy="8" r="4" fill="none" stroke="#e2cc6a" stroke-width="1"/><path d="M4 8h8M8 4v8" stroke="#e2cc6a" stroke-width="1"/></svg>www.ambercoachline.co.uk</span>
  </div>
  <div class="abs brand" style="top:494px"><span class="dot"></span>Amber Coachline</div>
</section>

</body>
</html>
```